Personal Injury Lawyer Billboard

I would like a design created featuring the image of the lawyer centered in the middle of the design.
To the left of the lawyer's image it should read "INJURED?"
To the right of the lawyer's image, it should read "CALL DEAN!"
Under Call Dean, include the phone number 318-555-0187.
At the bottom of the design include the lawyers information "Dean Marlowe Accident & Injury Lawyers"
PLEASE REMOVED THE BACKGROUND IMAGERY OF THE PHOTO SUBMITTED. Also, the colors for this design should match the colors shown in the logo (navy, white and relective soft gold). Please use those color combinations in ways that best stand out.

```html
<!DOCTYPE html>
<html lang="en">
<head>
<meta charset="utf-8">
<title>Dean Marlowe Accident &amp; Injury Lawyers — Billboard</title>
<link rel="stylesheet" href="https://fonts.googleapis.com/css2?family=Libre+Baskerville:wght@400;700&display=swap">
<style>
  :root {
    --navy: #14234b;
    --navy-band: #0d1a3d;
    --gold: #c6a04a;
    --white: #ffffff;
  }
  html, body {
    margin: 0;
    padding: 0;
    width: 1200px;
    height: 600px;
    overflow: hidden;
    background: var(--navy);
  }
  .billboard {
    display: block;
    width: 1200px;
    height: 600px;
    font-family: "Libre Baskerville", Georgia, serif;
  }
  .headline {
    font-weight: 700;
    fill: var(--white);
    stroke: var(--gold);
    stroke-width: 5px;
    paint-order: stroke fill;
    stroke-linejoin: round;
  }
  .phone-number {
    font-weight: 700;
    fill: var(--white);
  }
  .firm-name { font-weight: 700; }
  .firm-name .firm-person { fill: var(--white); }
  .firm-name .firm-practice { fill: var(--gold); }
  .corner-name {
    font-weight: 400;
    fill: var(--white);
  }
</style>
</head>
<body>
<svg class="billboard" viewBox="0 0 1200 600" xmlns="http://www.w3.org/2000/svg">
  <defs>
    <linearGradient id="skyline-tone" x1="0" y1="0" x2="0" y2="1">
      <stop offset="0" stop-color="#17274f"/>
      <stop offset="1" stop-color="#0f1d42"/>
    </linearGradient>
    <radialGradient id="portrait-tone" cx="0.5" cy="0.4" r="0.6">
      <stop offset="0" stop-color="#2a3a66"/>
      <stop offset="1" stop-color="#182a56"/>
    </radialGradient>
  </defs>

  <!-- background -->
  <rect class="backdrop" width="1200" height="600" fill="url(#skyline-tone)" role="img" aria-label="Faint navy-tinted city skyline of office towers"/>

  <!-- gold frame -->
  <rect class="gold-frame" x="27" y="41" width="1145" height="518" fill="none" stroke="var(--gold)" stroke-width="1.5"/>

  <!-- lawyer portrait -->
  <path class="portrait" d="M420 14 H565 Q575 14 575 24 V232 H695 Q705 232 705 242 V518 H315 V242 Q315 232 325 232 H410 V24 Q410 14 420 14 Z" fill="url(#portrait-tone)" role="img" aria-label="Portrait of the lawyer in a navy suit, white shirt and green tie, smiling with a raised fist"/>

  <!-- left headline -->
  <text class="headline headline-left" x="52" y="204" font-size="74" textLength="342" lengthAdjust="spacingAndGlyphs">INJURED?</text>

  <!-- right headline -->
  <text class="headline headline-right" x="716" y="302" font-size="70" textLength="434" lengthAdjust="spacingAndGlyphs">CALL DEAN!</text>

  <!-- phone -->
  <g class="phone-line">
    <circle cx="796" cy="366" r="32" fill="none" stroke="var(--gold)" stroke-width="2"/>
    <path class="phone-icon" d="M783 352c2-2 4-2 5 0l4 6c1 2 0 3-1 4l-2 2c2 5 6 9 11 11l2-2c1-1 3-2 4-1l6 4c2 1 2 3 0 5l-3 3c-3 2-7 2-12-1-7-4-13-10-16-17-2-5-2-9 1-12z" fill="none" stroke="var(--gold)" stroke-width="2" stroke-linejoin="round"/>
    <text class="phone-number" x="839" y="384" font-size="50" textLength="307" lengthAdjust="spacingAndGlyphs">318-555-0187</text>
  </g>

  <!-- corner firm name -->
  <text class="corner-name" x="1156" y="86" font-size="18" text-anchor="end">Dean Marlowe</text>

  <!-- bottom firm band -->
  <rect class="firm-band" x="141" y="518" width="926" height="67" fill="var(--navy-band)"/>
  <text class="firm-name" x="161" y="566" font-size="38" textLength="888" lengthAdjust="spacingAndGlyphs"><tspan class="firm-person">Dean Marlowe </tspan><tspan class="firm-practice">Accident &amp; Injury Lawyers</tspan></text>
</svg>
</body>
</html>
```